Maple Bus Card

i own a building in the bronx ny - its called "Maple 7 on 2 HDFC"i want a classy logo / business card - nothing too religuous but it is like a family there - its a large apartment building - colors i like dark red, black, medium shade of gray also reg business card stuff tel # 914-555-0173 address 4738 Larkwell Ave Harlow Falls NY 12987 Email fijosh@aol.comslogan - " Together under one roof "i can send u a picture of the building for the backside

```html
<!DOCTYPE html>
<html lang="en">
<head>
<meta charset="utf-8">
<title>Maple 7 on 2 HDFC – Business Card</title>
<link href="https://fonts.googleapis.com/css2?family=Open+Sans:wght@400;700&display=swap" rel="stylesheet">
<style>
  :root {
    --brand-red: #b51d25;
    --deep-red: #8e1519;
    --ink: #1e1e1e;
    --band-gray: #efefef;
    --paper: #ffffff;
    --backdrop: #cdd0d4;
  }
  * { margin: 0; padding: 0; box-sizing: border-box; }
  html, body { width: 1200px; height: 900px; overflow: hidden; }
  body {
    background: var(--backdrop);
    font-family: "Open Sans", Arial, sans-serif;
    position: relative;
  }
  .card {
    position: absolute;
    left: 320px;
    width: 560px;
    height: 320px;
    border-radius: 18px;
    overflow: hidden;
    box-shadow: 0 8px 22px rgba(0,0,0,0.18);
  }
  .card--front { top: 100px; background: var(--paper); }
  .card--back { top: 480px; }

  .front__identity {
    position: absolute;
    top: 58px;
    left: 150px;
    right: 40px;
    text-align: center;
  }
  .front__company {
    font-family: "Open Sans", Arial, sans-serif;
    font-weight: 700;
    color: var(--brand-red);
    font-size: 30px;
    line-height: 1.1;
    white-space: nowrap;
  }
  .front__slogan {
    margin-top: 8px;
    font-size: 11px;
    letter-spacing: 0.3px;
    color: var(--ink);
    text-transform: uppercase;
  }
  .front__name-band {
    position: absolute;
    left: 0; right: 0;
    top: 140px;
    height: 78px;
    background: var(--band-gray);
  }
  .front__person {
    position: absolute;
    top: 154px;
    left: 150px;
    right: 40px;
    text-align: center;
  }
  .front__name {
    font-weight: 700;
    font-size: 22px;
    color: var(--ink);
    text-transform: uppercase;
    line-height: 1.1;
  }
  .front__position {
    font-size: 15px;
    color: var(--brand-red);
    text-transform: uppercase;
  }
  .front__contacts {
    position: absolute;
    top: 232px;
    left: 28px;
    right: 28px;
    display: flex;
    justify-content: space-between;
    align-items: center;
  }
  .contact {
    display: flex;
    align-items: center;
    gap: 10px;
    font-size: 19px;
    color: var(--ink);
  }
  .contact__icon { width: 22px; height: 22px; flex: none; }
  .front__address-band {
    position: absolute;
    left: 0; right: 0; bottom: 0;
    height: 46px;
    background: var(--brand-red);
    display: flex;
    align-items: center;
    padding-left: 28px;
    gap: 8px;
    color: var(--paper);
    font-size: 16px;
  }
  .address__icon { width: 12px; height: 16px; }

  .back__building {
    width: 100%;
    height: 100%;
    background: linear-gradient(135deg, #a91c22 0%, var(--deep-red) 100%);
  }
</style>
</head>
<body>

<section class="card card--front" aria-label="Business card front">
  <div class="front__identity">
    <h1 class="front__company">Maple 7 on 2 HDFC</h1>
    <p class="front__slogan">Together under one roof</p>
  </div>

  <div class="front__name-band"></div>
  <div class="front__person">
    <p class="front__name">Your Name</p>
    <p class="front__position">Position</p>
  </div>

  <div class="front__contacts">
    <p class="contact contact--phone">
      <svg class="contact__icon" viewBox="0 0 22 22" aria-hidden="true">
        <circle cx="11" cy="11" r="11" fill="var(--brand-red)"/>
        <path d="M8 6.5c.6-.4 1.2-.2 1.5.4l.8 1.6c.2.5.1 1-.3 1.3l-.6.5c.5 1.2 1.4 2.1 2.6 2.6l.5-.6c.3-.4.8-.5 1.3-.3l1.6.8c.6.3.8.9.4 1.5l-.6.9c-.5.7-1.4.9-2.2.6-2.8-1-4.9-3.1-5.900-5.9-.3-.8-.1-1.7.6-2.2z" fill="#fff"/>
      </svg>
      914-555-0173
    </p>
    <p class="contact contact--email">
      <svg class="contact__icon" viewBox="0 0 22 22" aria-hidden="true">
        <circle cx="11" cy="11" r="11" fill="var(--brand-red)"/>
        <rect x="5.5" y="7.5" width="11" height="7.5" rx="1" fill="none" stroke="#fff" stroke-width="1.4"/>
        <path d="M5.8 8l5.2 4 5.2-4" fill="none" stroke="#fff" stroke-width="1.4"/>
      </svg>
      mavreld@quintmail.com
    </p>
  </div>

  <div class="front__address-band">
    <svg class="address__icon" viewBox="0 0 12 16" aria-hidden="true">
      <path d="M6 0C2.7 0 0 2.6 0 5.9 0 10 6 16 6 16s6-6 6-10.1C12 2.6 9.3 0 6 0z" fill="#fff"/>
      <circle cx="6" cy="5.8" r="2.2" fill="var(--brand-red)"/>
    </svg>
    <span class="address__text">4738 Larkwell Ave, Harlow Falls NY 12987</span>
  </div>
</section>

<section class="card card--back" aria-label="Business card back">
  <div class="back__building" role="img" aria-label="Illustration of the red brick apartment building entrance with a gold-paned door and name sign above"></div>
</section>

</body>
</html>
```